Harborline Auto LLC

Car Dealer Customer Service
Address: 2874 Cresthaven Road, Shelbyville, TN 37162
web: www.harborlineautoxq.net
email: harborlineautoxq@mailnest.example
Phone: (931) 555-0148
Phone: (629) 555-0173

```html
<!DOCTYPE html>
<html lang="en">
<head>
<meta charset="utf-8">
<title>Harborline Auto – Business Card</title>
<link rel="stylesheet" href="https://fonts.googleapis.com/css2?family=Poppins:wght@400;600;700&display=swap">
<style>
  :root {
    --page-bg: #e7e4e0;
    --card-blue: #1f84ad;
    --card-blue-deep: #17698d;
    --frost: #eef3f5;
    --gold: #e4a334;
    --brand-blue: #1c5f82;
    --text-light: #f2f7fa;
    --text-soft: #dcebf2;
  }
  html, body {
    margin: 0;
    width: 1200px;
    height: 1054px;
    overflow: hidden;
    background: var(--page-bg);
    font-family: "Poppins", sans-serif;
  }
  .card {
    position: absolute;
    left: 75px;
    top: 209px;
    width: 1050px;
    height: 636px;
    border-radius: 28px;
    overflow: hidden;
    background: linear-gradient(160deg, var(--card-blue) 0%, var(--card-blue-deep) 100%);
    box-shadow: 0 18px 40px rgba(0,0,0,0.18);
  }
  .card-shapes {
    position: absolute;
    inset: 0;
  }
  .holder-name {
    position: absolute;
    left: 50px;
    top: 62px;
    margin: 0;
    font-size: 37px;
    font-weight: 700;
    color: var(--gold);
  }
  .holder-title {
    position: absolute;
    left: 50px;
    top: 114px;
    margin: 0;
    font-size: 26px;
    font-weight: 400;
    color: var(--text-light);
  }
  .contact-list {
    position: absolute;
    left: 50px;
    top: 382px;
    margin: 0;
    padding: 0;
    list-style: none;
  }
  .contact-item {
    display: flex;
    align-items: center;
    gap: 16px;
    height: 36px;
    font-size: 25px;
    color: var(--text-light);
  }
  .contact-item svg { width: 22px; height: 22px; flex: none; }
  .contact-item.phone { font-weight: 600; color: var(--gold); }
  .contact-item.web { margin-top: 10px; }
  .address {
    position: absolute;
    left: 50px;
    top: 538px;
    margin: 0;
    font-size: 25px;
    color: var(--text-soft);
  }
  .brand-name {
    position: absolute;
    left: 560px;
    width: 480px;
    top: 300px;
    margin: 0;
    text-align: center;
    font-size: 40px;
    font-weight: 700;
    letter-spacing: 1px;
    color: var(--brand-blue);
  }
</style>
</head>
<body>
  <section class="card">
    <svg class="card-shapes" viewBox="0 0 1050 636" width="1050" height="636" aria-hidden="true">
      <path d="M505 0 C468 110 458 290 560 380 C650 460 860 490 1050 462 L1050 490 C850 520 630 490 540 395 C440 290 450 110 488 0 Z" fill="var(--gold)"/>
      <path d="M515 0 L1050 0 L1050 462 C860 490 650 460 560 380 C458 290 468 110 515 0 Z" fill="var(--frost)"/>
    </svg>

    <h1 class="holder-name">Daniel Reeve</h1>
    <p class="holder-title">Managing Director</p>

    <ul class="contact-list">
      <li class="contact-item phone">
        <svg viewBox="0 0 24 24"><path fill="var(--gold)" d="M6.6 10.8a15.1 15.1 0 0 0 6.6 6.6l2.2-2.2a1 1 0 0 1 1-.25 11.4 11.4 0 0 0 3.6.57 1 1 0 0 1 1 1V20a1 1 0 0 1-1 1A17 17 0 0 1 3 4a1 1 0 0 1 1-1h3.5a1 1 0 0 1 1 1c0 1.25.2 2.45.57 3.57a1 1 0 0 1-.25 1z"/></svg>
        931-555-0148
      </li>
      <li class="contact-item phone">
        <svg viewBox="0 0 24 24"><path fill="var(--gold)" d="M6.6 10.8a15.1 15.1 0 0 0 6.6 6.6l2.2-2.2a1 1 0 0 1 1-.25 11.4 11.4 0 0 0 3.6.57 1 1 0 0 1 1 1V20a1 1 0 0 1-1 1A17 17 0 0 1 3 4a1 1 0 0 1 1-1h3.5a1 1 0 0 1 1 1c0 1.25.2 2.45.57 3.57a1 1 0 0 1-.25 1z"/></svg>
        629-555-0173
      </li>
      <li class="contact-item web">
        <svg viewBox="0 0 24 24"><rect x="2" y="5" width="20" height="14" rx="1.5" fill="var(--gold)"/><path d="M3 6l9 7 9-7" fill="none" stroke="var(--card-blue)" stroke-width="1.8"/></svg>
        www.harborlineautoxq.net
      </li>
      <li class="contact-item email">
        <svg viewBox="0 0 24 24"><circle cx="12" cy="12" r="9.5" fill="none" stroke="var(--gold)" stroke-width="2"/><path d="M2.5 12h19M12 2.5c3 3 3 16 0 19M12 2.5c-3 3-3 16 0 19" fill="none" stroke="var(--gold)" stroke-width="1.6"/></svg>
        harborlineautoxq@mailnest.example
      </li>
    </ul>

    <p class="address">2874 Cresthaven Road, Shelbyville, TN 37162</p>

    <p class="brand-name">HARBORLINE AUTO</p>
  </section>
</body>
</html>
```